Business Card for Professional Photographer

I'm looking for an eye catching modern clean design that compliments my logo/ website fonts & colours.
I specialise in architecture, corporate & commercial photography so I'm marketing to professional clients rather than portrait / wedding clients.

I would prefer to not have a solid black design.

My logo brand guide is as follows :

Main front font. : Reislust
Main font colour : #fff
Slogan front font : Ubuntu Bold
Monogram front font : Venti Medium
Container colour : #fff

I need print ready files in pdf .png & .eps formats.

Included in the files below are some screen grabs as reference to font & colours etc.

```html
<!DOCTYPE html>
<html lang="en">
<head>
<meta charset="utf-8">
<title>Clear Frame Studio – Business Card</title>
<link rel="stylesheet" href="https://fonts.googleapis.com/css2?family=Ubuntu:wght@300;400;500&display=swap">
<style>
  :root {
    --backdrop: #e6e3df;
    --card: #ffffff;
    --gold: #c9985a;
    --gold-light: #e7cf94;
    --ink: #4a4541;
    --ink-soft: #8a847e;
    --shadow: rgba(40, 30, 20, 0.18);
  }
  * { margin: 0; padding: 0; box-sizing: border-box; }
  html, body {
    width: 1200px;
    height: 716px;
    overflow: hidden;
    background: var(--backdrop);
    font-family: "Ubuntu", sans-serif;
  }
  .sheet {
    position: relative;
    width: 1200px;
    height: 716px;
    display: flex;
    align-items: center;
    justify-content: center;
    gap: 40px;
  }
  .card {
    position: relative;
    width: 525px;
    height: 300px;
    background: var(--card);
    box-shadow: 0 8px 24px var(--shadow);
    overflow: hidden;
  }

  /* brand wordmark */
  .wordmark {
    font-family: "Ubuntu", sans-serif;
    font-weight: 300;
    color: var(--ink-soft);
    text-transform: uppercase;
    letter-spacing: 0.24em;
    white-space: nowrap;
  }
  .tagline {
    font-weight: 500;
    color: var(--ink-soft);
    letter-spacing: 0.28em;
    font-size: 6.5px;
    margin-top: 4px;
    white-space: nowrap;
  }

  /* front: contact side */
  .card-front .brand {
    position: absolute;
    left: 34px;
    top: 30px;
  }
  .card-front .wordmark { font-size: 19px; }
  .contact {
    position: absolute;
    left: 34px;
    top: 118px;
    color: var(--ink);
  }
  .contact .person-name {
    font-size: 17px;
    font-weight: 400;
    color: var(--gold);
  }
  .contact .person-role {
    font-size: 10.5px;
    margin-top: 2px;
  }
  .contact address {
    font-style: normal;
    font-size: 10.5px;
    line-height: 1.35;
    margin-top: 10px;
  }
  .contact-list {
    list-style: none;
    margin-top: 8px;
    font-size: 10.5px;
    line-height: 1.4;
  }
  .contact-list li {
    display: flex;
    align-items: center;
    gap: 6px;
  }
  .contact-list svg {
    width: 9px;
    height: 9px;
    fill: none;
    stroke: var(--gold);
    stroke-width: 1.6;
  }
  .front-accent {
    position: absolute;
    right: 0;
    top: 0;
    width: 6px;
    height: 100%;
    background: linear-gradient(180deg, var(--gold), var(--gold-light), var(--gold));
  }

  /* back: brand side */
  .card-back .brand {
    position: absolute;
    right: 52px;
    top: 50%;
    transform: translateY(-50%);
    display: flex;
    align-items: center;
    gap: 14px;
  }
  .card-back .brand-dot {
    width: 44px;
    height: 44px;
    border-radius: 50%;
    border: 4px solid var(--gold);
    flex: none;
  }
  .card-back .wordmark {
    font-size: 20px;
    color: var(--gold);
  }
  .card-back .tagline { color: var(--gold); }
  .back-accent {
    position: absolute;
    left: 0;
    top: 0;
    width: 6px;
    height: 100%;
    background: linear-gradient(180deg, var(--gold), var(--gold-light), var(--gold));
  }
</style>
</head>
<body>
<main class="sheet">
  <section class="card card-front" aria-label="Card front">
    <div class="brand">
      <div class="wordmark">Clear Frame Studio</div>
      <div class="tagline">Architecture Corporate Commercial</div>
    </div>

    <div class="contact">
      <h1 class="person-name">Daniel Harper</h1>
      <p class="person-role">President</p>
      <address>1420 Birchwood Drive<br>Juneau, Alaska 99801</address>
      <ul class="contact-list">
        <li>
          <svg viewBox="0 0 10 10"><path d="M2 1 L4 1 L4.5 3 L3.4 4 Q4.5 6 6 6.6 L7 5.5 L9 6 L9 8 Q5 9 1.5 4.5 Q1 2.5 2 1 Z"/></svg>
          555-214-7730
        </li>
        <li>
          <svg viewBox="0 0 10 10"><rect x="2.5" y="0.8" width="5" height="8.4" rx="0.8"/></svg>
          555-318-6402
        </li>
        <li>
          <svg viewBox="0 0 10 10"><rect x="1" y="3.5" width="8" height="4.5"/><rect x="3" y="1" width="4" height="2.5"/></svg>
          555-427-9915
        </li>
        <li>
          <svg viewBox="0 0 10 10"><rect x="1" y="2" width="8" height="6"/><path d="M1 2 L5 5.5 L9 2"/></svg>
          hello@clearframestudio.com
        </li>
        <li>
          <svg viewBox="0 0 10 10"><circle cx="5" cy="5" r="4"/><path d="M1 5 H9 M5 1 Q2.5 5 5 9 Q7.5 5 5 1"/></svg>
          www.clearframestudio.com
        </li>
      </ul>
    </div>
    <div class="front-accent"></div>
  </section>

  <section class="card card-back" aria-label="Card back">
    <div class="back-accent"></div>
    <div class="brand">
      <span class="brand-dot"></span>
      <div>
        <div class="wordmark">Clear Frame Studio</div>
        <div class="tagline">Architecture Corporate Commercial</div>
      </div>
    </div>
  </section>
</main>
</body>
</html>
```